Business Card Design - VNT (company name)

Over 20 years of progressive technology design, migration and management experience that drives business objectives and streamlines operations. Continuously challenge conventions to meet and exceed business security, availability and functionality requirements. Maintain exceptional vendor relationships to ensure ongoing knowledge of emerging products and to secure preferred service agreements. Recruit and utilize top talent and foster a collegial environment that advances innovation and performance excellence. design logo using 3 arrows of different colors green, gold, blue

Industry/Entity Type

Progressive

Contact Information for Business Card

Martin K. Osgood
IT Strategist / Consultant

626.583.2907 MOsgood@vntosgood.example 4817 Brenning Court Pasadena, CA 91104

Colors
0255a3
f37122
fece3e

Requirements
Must have
• Note NEW EMAIL ADDRESS
• MOsgood@vntosgood.example
• NOTE NEW ORDER of the work I do.
• Infrastructure – Systems – Cybersecurity
Nice to have
• main color should be orange

```html
<!DOCTYPE html>
<html lang="en">
<head>
<meta charset="utf-8">
<title>VNT Business Card</title>
<link href="https://fonts.googleapis.com/css2?family=Carlito:wght@400;700&display=swap" rel="stylesheet">
<style>
  :root {
    --backdrop: #3a3633;
    --card: #1c1d1f;
    --text: #f2f2f2;
    --text-soft: #d9d9d9;
    --divider: #3c3d40;
    --brand-orange: #f37122;
    --brand-blue: #0255a3;
    --brand-gold: #fece3e;
    --silver: #bdbdbd;
  }
  * { margin: 0; padding: 0; box-sizing: border-box; }
  html, body {
    width: 1200px;
    height: 844px;
    overflow: hidden;
    background: var(--backdrop);
    font-family: "Carlito", "Calibri", sans-serif;
  }
  .canvas {
    position: relative;
    width: 1200px;
    height: 844px;
  }
  .card {
    position: absolute;
    top: 272px;
    width: 525px;
    height: 300px;
    background: var(--card);
    border-radius: 4px;
    box-shadow: 0 10px 28px rgba(0,0,0,0.45);
  }
  .card--front { left: 50px; }
  .card--back  { left: 625px; }

  .front-brand {
    position: absolute;
    left: 0;
    top: 0;
    width: 235px;
    height: 100%;
    display: flex;
    align-items: center;
    justify-content: center;
    gap: 12px;
  }
  .brand-dot {
    width: 22px;
    height: 22px;
    border-radius: 50%;
    background: var(--brand-gold);
  }
  .brand-name {
    font-weight: 700;
    font-size: 62px;
    letter-spacing: 2px;
    color: var(--brand-orange);
    line-height: 1;
  }
  .divider {
    position: absolute;
    left: 240px;
    top: 40px;
    width: 1px;
    height: 220px;
    background: var(--divider);
  }
  .contact {
    position: absolute;
    left: 270px;
    top: 42px;
    width: 240px;
    color: var(--text);
  }
  .contact__name {
    font-weight: 700;
    font-size: 25px;
    line-height: 1.05;
  }
  .contact__title {
    font-size: 14px;
    line-height: 1.3;
    color: var(--text-soft);
  }
  .contact__services {
    font-size: 13px;
    line-height: 1.3;
    color: var(--brand-orange);
    margin-bottom: 16px;
  }
  .contact__lines {
    font-size: 15px;
    line-height: 1.3;
    list-style: none;
    margin-bottom: 12px;
  }
  .contact__address {
    font-style: normal;
    font-size: 15px;
    line-height: 1.3;
  }

  .back-brand {
    position: absolute;
    inset: 0;
    display: flex;
    align-items: center;
    justify-content: center;
    padding-bottom: 40px;
  }
  .back-brand .brand-name {
    color: var(--silver);
    font-size: 76px;
  }
</style>
</head>
<body>
  <main class="canvas">
    <section class="card card--front">
      <div class="front-brand">
        <span class="brand-dot"></span>
        <span class="brand-name">VNT</span>
      </div>
      <div class="divider"></div>
      <div class="contact">
        <h1 class="contact__name">Martin K. Osgood</h1>
        <p class="contact__title">IT Strategist / Consultant</p>
        <p class="contact__services">Infrastructure – Systems – Cybersecurity</p>
        <ul class="contact__lines">
          <li>T: 626.583.2907</li>
          <li>E: MOsgood@vntosgood.example</li>
          <li>W: www.vntosgood.example</li>
        </ul>
        <address class="contact__address">
          4817 Brenning Court<br>
          Pasadena, CA 91104
        </address>
      </div>
    </section>

    <section class="card card--back">
      <div class="back-brand">
        <span class="brand-name">VNT</span>
      </div>
    </section>
  </main>
</body>
</html>
```